VFX Company Business Card Design Project

The Kestrel Works is a decentralized Visual Effects Studio servicing the television and feature film industries.
Project Brief:
Take our logo that was previously designed on Pencil Harbor and make a double sided business card.
Requirements:
- Card MUST be double sided.
- Front of card MUST have the yellow part of our logo against the dark grey background.
- Back of card is completely up to the designer.
- Back of card must include the complete company logo.
Please follow these File Preparation guidelines:
http://printnook.ca/infopage?file=filetype_en&s=PrintNook_new&lang=en
Business

```html
<!DOCTYPE html>
<html lang="en">
<head>
<meta charset="utf-8">
<title>The Kestrel Works – Business Cards</title>
<link rel="stylesheet" href="https://fonts.googleapis.com/css2?family=Jost:wght@400;500&family=PT+Sans:wght@400;700&display=swap">
<style>
  :root {
    --backdrop: #8c4a22;
    --card: #272727;
    --brand-yellow: #ffc425;
    --ink-light: #f1f2ea;
    --ink-grey: #5f6a6e;
    --rule: #d9d9d9;
  }
  * { box-sizing: border-box; margin: 0; padding: 0; }
  html, body { width: 1200px; height: 734px; overflow: hidden; }
  body {
    position: relative;
    background: var(--backdrop);
    font-family: "PT Sans", Arial, sans-serif;
    color: var(--ink-light);
  }
  .card {
    position: absolute;
    width: 524px;
    height: 299px;
    background: var(--card);
  }
  .card--front { left: 67px; top: 43px; }
  .card--contact { left: 628px; top: 48px; }
  .card--lockup { left: 63px; top: 381px; }
  .card--wordmark { left: 622px; top: 387px; }

  .brand-name {
    position: absolute;
    font-family: "Jost", "Futura", sans-serif;
    font-weight: 500;
    white-space: nowrap;
    letter-spacing: 0.01em;
  }
  .card--front .brand-name {
    left: 0; right: 0; top: 118px;
    text-align: center;
    font-size: 44px;
    color: var(--brand-yellow);
  }
  .card--contact .brand-name {
    left: 42px; top: 44px;
    font-size: 34px;
    color: var(--ink-light);
  }
  .card--lockup .brand-name {
    left: 104px; top: 118px;
    font-size: 38px;
    color: var(--ink-light);
  }
  .brand-dot {
    position: absolute;
    left: 40px; top: 116px;
    width: 50px; height: 50px;
    border-radius: 50%;
    background: var(--brand-yellow);
  }
  .card--wordmark .brand-name {
    left: 0; right: 0; top: 102px;
    text-align: center;
    font-size: 50px;
    color: var(--ink-light);
  }

  .web-address {
    position: absolute;
    left: 0; right: 0;
    text-align: center;
    font-family: "Jost", "Futura", sans-serif;
    font-size: 18px;
    letter-spacing: 0.14em;
    color: var(--ink-light);
  }
  .card--lockup .web-address { top: 256px; }
  .card--wordmark .web-address { top: 256px; }

  .person { position: absolute; left: 42px; top: 180px; }
  .person__name { font-size: 19px; font-weight: 700; line-height: 1.2; }
  .person__title { font-size: 15px; line-height: 1.4; }
  .card--contact .contact-web {
    position: absolute; left: 42px; top: 263px;
    font-size: 14px;
  }
  .divider {
    position: absolute;
    left: 262px; top: 184px;
    width: 1px; height: 115px;
    background: var(--rule);
  }
  .contact-list {
    position: absolute;
    left: 278px; top: 180px;
    list-style: none;
    font-size: 14px;
    line-height: 20.5px;
  }
  .contact-list li { display: flex; align-items: flex-start; gap: 6px; }
  .contact-list li.contact-address { margin-top: 13px; }
  .contact-list svg { flex: none; margin-top: 5px; width: 11px; height: 11px; fill: var(--ink-light); }
</style>
</head>
<body>
  <section class="card card--front" aria-label="Card front">
    <div class="brand-name">The Kestrel Works</div>
  </section>

  <section class="card card--contact" aria-label="Card back with contact details">
    <div class="brand-name">The Kestrel Works</div>
    <div class="person">
      <p class="person__name">Your Name</p>
      <p class="person__title">Title</p>
    </div>
    <p class="contact-web">www.kestrelworks.com</p>
    <div class="divider"></div>
    <ul class="contact-list">
      <li>
        <svg viewBox="0 0 12 12" aria-hidden="true"><path d="M2.5 0.8 4.3 3 3.3 4.4c.8 1.8 2.2 3.2 4 4l1.4-1 2.2 1.8-.9 1.9C5 11 1 7 .6 1.7z"/></svg>
        <span>0987 654321</span>
      </li>
      <li>
        <svg viewBox="0 0 12 12" aria-hidden="true"><rect x="3" y="0.5" width="6" height="11" rx="1.2"/></svg>
        <span>0987 654321</span>
      </li>
      <li>
        <svg viewBox="0 0 12 12" aria-hidden="true"><path d="M0.5 2.5h11v7h-11z M1 3l5 3.5L11 3" stroke="#272727" stroke-width="0.9"/></svg>
        <span>info@kestrelworks.com</span>
      </li>
      <li class="contact-address">
        <svg viewBox="0 0 12 12" aria-hidden="true"><circle cx="6" cy="6" r="5.5"/><circle cx="6" cy="5" r="1.6" fill="#272727"/></svg>
        <span>00, Complex name<br>City, State 0042</span>
      </li>
    </ul>
  </section>

  <section class="card card--lockup" aria-label="Card back with brand lockup">
    <div class="brand-dot"></div>
    <div class="brand-name">The Kestrel Works</div>
    <p class="web-address">www.kestrelworks.com</p>
  </section>

  <section class="card card--wordmark" aria-label="Card back with brand name">
    <div class="brand-name">The Kestrel Works</div>
    <p class="web-address">www.kestrelworks.com</p>
  </section>
</body>
</html>
```